Edit and Update existing catalog

I have a 60 paged catalog that needs to have some changes. We are adding around 20 pages, changing another 15 pages, and also have 10 pages that need to be graphically designed and inserted. The current existing catalog is included as well as a PDF explaining all the changes (Catalog Changes.pdf), as well as all the pages that need to be added and our logo.

Target Market(s)

physician offices and professional healthcare providers

Industry/Entity Type

Healthcare

Colors
0054AA
0677BA
7BADD7
CADEEF
E8F1F8

Requirements
Must have
• Additional pages must match the format of the existing catalog
Should not have
• No protected health information - all patient names, Date of births and accession #s should be removed, incase they are not please replace with XXX on the reports.

```html
<!DOCTYPE html>
<html lang="en">
<head>
<meta charset="utf-8">
<title>Harbor Point Labs – Catalog Page Spreads</title>
<link href="https://fonts.googleapis.com/css2?family=Montserrat:ital,wght@0,600;0,700;0,800;1,800&family=Open+Sans:wght@400;600;700&display=swap" rel="stylesheet">
<style>
:root{
  --navy:#0054AA;
  --blue:#0677BA;
  --sky:#7BADD7;
  --pale:#CADEEF;
  --mist:#E8F1F8;
  --ink:#2b2b2b;
  --grey:#555;
  --strip:#333333;
  --board:#c9c9c9;
  --red:#e0262b;
  --yellow:#f6e21a;
  --lav:#9b6fc0;
}
*{box-sizing:border-box;margin:0;padding:0}
html,body{width:720px;height:1200px;overflow:hidden;background:var(--board);font-family:"Open Sans",Arial,sans-serif;color:var(--ink)}
.board{position:relative;width:720px;height:1200px}
.page{position:absolute;width:156px;height:190px;background:#fff;overflow:hidden}
.c1{left:21px}.c2{left:195px}.c3{left:369px}.c4{left:543px}
.r1{top:85px}.r2{top:295px}.r3{top:505px}.r4{top:715px}.r5{top:925px}

.tab-top,.tab-bottom{position:absolute;left:0;right:0;height:10px;background:var(--strip);color:#fff;font-size:2.6px;display:flex;align-items:center;justify-content:center}
.tab-top{top:0}
.tab-bottom{bottom:0;transform:rotate(180deg)}
.tab-side{position:absolute;top:0;bottom:0;width:10px;background:var(--strip);color:#fff;font-size:2.6px}
.tab-side.right{right:0}.tab-side.left{left:0}
.tab-side span{position:absolute;top:50%;left:50%;white-space:nowrap;transform:translate(-50%,-50%) rotate(90deg)}
.folio{position:absolute;bottom:3px;font-size:2.4px;color:#666}
.folio.l{left:14px}.folio.r{right:14px}
.edge{position:absolute;right:0;top:10px;width:7px;bottom:0;background:linear-gradient(var(--blue),var(--navy))}

.rot{position:absolute;transform:rotate(-90deg);transform-origin:left top;white-space:nowrap}
.guide-title{font-family:"Montserrat",sans-serif;font-weight:800;font-style:italic;font-size:5px;color:var(--ink)}
.guide-sub{font-size:2.6px;font-weight:700;font-style:italic}
.brand{font-family:"Montserrat",sans-serif;font-weight:700;color:var(--navy);display:flex;align-items:center;gap:2px;white-space:nowrap}
.brand i{display:inline-block;border-radius:50%;background:var(--navy);flex:none}
.brand.white{color:#fff}.brand.white i{background:#fff}

.t{font-size:2.2px;line-height:1.35}
.tt{font-size:1.85px;line-height:1.3}
.h{font-family:"Montserrat",sans-serif;font-weight:700;color:var(--blue)}
.band{background:var(--blue);color:#fff;font-size:2.3px;font-weight:700;text-align:center;padding:.3px 0}
.band.sky{background:var(--sky)}
.pill{display:inline-block;background:var(--blue);color:#fff;font-size:2.2px;font-weight:700;padding:.4px 3px;border-radius:1.5px;margin:2px 0 1px}
.img{background:linear-gradient(150deg,#eef1f4,#b9c4cf 60%,#8797a6)}

/* specimen grid */
.spec{position:absolute;left:40px;top:14px;width:100px;height:170px;display:grid;grid-template-columns:repeat(3,1fr);grid-template-rows:repeat(4,1fr);border:.5px solid #444}
.spec>div{border:.3px solid #777;padding:1.5px;display:flex;gap:1.5px}
.spec b{writing-mode:vertical-rl;transform:rotate(180deg);font-size:2.1px}
.spec .ph{width:12px;flex:none;border-radius:1px;background:linear-gradient(90deg,#e9e9e9,#c2d1e1)}
.spec .tt{flex:1}

/* blood guide */
.blood{position:absolute;left:42px;top:12px;width:100px;height:176px;display:grid;grid-template-columns:repeat(6,1fr);border:.5px solid #444}
.blood>div{border-right:.3px solid #444;display:flex;flex-direction:column}
.blood .tube{height:28px;margin:2px 4px;border-radius:2px;background:linear-gradient(#fff 0 20%,#ddd 20% 70%,var(--c,#aaa) 70%)}
.blood .hd{font-size:2.4px;font-weight:700;text-align:center;padding:1px 0}
.blood .tt{flex:1;padding:1px}
.blood .lb{font-family:"Montserrat",sans-serif;font-weight:800;font-size:3.4px;text-align:center;padding:2px 0}
.y{background:var(--yellow)}.rd{background:var(--red);color:#fff}.lv{background:#d8c8ea}.bl{background:#2a5bd7;color:#fff}

/* forms and tables */
.form-row{display:grid;border-bottom:.3px solid #9fb4c9;font-size:1.9px;font-weight:700;padding:.4px 1px;min-height:3px}
.drugs{column-gap:2px;font-size:1.7px;line-height:1.25;background:var(--mist);padding:1px}
.drugs p{break-inside:avoid;margin-bottom:1.2px;border-bottom:.2px solid #b8cbe0}
.drugs b{display:block;font-weight:700}
.drugs .sec{background:var(--sky);color:#fff;font-weight:700;text-align:center;margin:1px 0}
.codes{display:grid;grid-template-columns:repeat(8,1fr);font-size:1.7px;line-height:1.35;padding:1px;background:var(--mist)}

.summary{display:grid;gap:.4px;background:#fff}
.summary>div{background:var(--mist);font-size:1.7px;line-height:1.25;padding:1px;color:#444}
.summary .cat{background:var(--blue);color:#fff;font-weight:700;writing-mode:vertical-rl;transform:rotate(180deg);text-align:center;font-size:2px}
.summary .alt{background:var(--pale)}
.red{color:var(--red)}
</style>
</head>
<body>
<main class="board">

<!-- Page 17: specimen guide -->
<section class="page c1 r1">
  <div class="tab-top">Tabs Here - This portion will be trimmed off</div>
  <div class="edge"></div>
  <div class="rot guide-title" style="left:13px;top:128px">Specimen Collection Reference Guide</div>
  <div class="rot guide-sub" style="left:20px;top:113px">Questions? Call 555 014 2290</div>
  <div class="rot brand" style="left:26px;top:184px;font-size:6px"><i style="width:6px;height:6px"></i>Harbor Point Labs</div>
  <div class="spec">
    <div><b>Swab Kit</b><span class="ph" role="img" aria-label="Swab kit"></span><p class="tt">Nasal swab, place in media, label tube, store cold.</p></div>
    <div><b>Urine Cup</b><span class="ph" role="img" aria-label="Urine cup"></span><p class="tt">Clean catch, 30 mL minimum, seal lid tight.</p></div>
    <div><b>Blood Tube</b><span class="ph" role="img" aria-label="Blood tube"></span><p class="tt">Gold top, spin after 30 min, refrigerate.</p></div>
    <div><b>Culture Vial</b><span class="ph" role="img" aria-label="Culture vial"></span><p class="tt">Aerobic and anaerobic, fill to line.</p></div>
    <div><b>Transport Kit</b><span class="ph" role="img" aria-label="Transport kit"></span><p class="tt">Place sample in bag, add form to pocket.</p></div>
    <div><b>Stool Kit</b><span class="ph" role="img" aria-label="Stool container"></span><p class="tt">Fill to line, keep at room temperature.</p></div>
    <div><b>Sputum Cup</b><span class="ph" role="img" aria-label="Sputum cup"></span><p class="tt">Early morning deep cough, sterile cup.</p></div>
    <div><b>Buccal Swab</b><span class="ph" role="img" aria-label="Buccal swab"></span><p class="tt">Rub cheek 30 seconds, air dry swab.</p></div>
    <div><b>Viral Media</b><span class="ph" role="img" aria-label="Viral media"></span><p class="tt">Break swab into tube, cap and label.</p></div>
    <div><b>Wound Swab</b><span class="ph" role="img" aria-label="Wound swab"></span><p class="tt">Clean site, swab deep tissue edge.</p></div>
    <div><b>24 Hr Jug</b><span class="ph" role="img" aria-label="Urine jug"></span><p class="tt">Collect all urine, keep jug cold.</p></div>
    <div><b>Dry Swab</b><span class="ph" role="img" aria-label="Dry swab"></span><p class="tt">Collect, return to sleeve, ship same day.</p></div>
  </div>
</section>

<section class="page c2 r1">
  <div class="tab-bottom">Tabs Here - This portion will be trimmed off</div>
</section>

<!-- Page 19: blood guide -->
<section class="page c3 r1">
  <div class="tab-top">Tabs Here - This portion will be trimmed off</div>
  <div class="edge"></div>
  <div class="rot guide-title" style="left:13px;top:124px">Blood Collection Reference Guide</div>
  <div class="rot guide-sub" style="left:20px;top:110px">Questions? Call 555 014 2290</div>
  <div class="rot brand" style="left:26px;top:184px;font-size:6px"><i style="width:6px;height:6px"></i>Harbor Point Labs</div>
  <div class="blood">
    <div><span class="tube" style="--c:#a77bd0" role="img" aria-label="Lavender top tube"></span><span class="hd lv">Lavender</span><p class="tt">CBC w/ diff, A1C, ESR, Sed Rate, Blood Type, Retic, Lead, Platelets</p><span class="lb y">DON'T SPIN</span></div>
    <div><span class="tube" style="--c:#d9b21c" role="img" aria-label="Gold top tube"></span><span class="hd y">Gold SST</span><p class="tt">CMP, BMP, Lipid, TSH, T3, T4, Vitamin D, B12, Folate, Iron, PSA, Hepatic</p><span class="lb y">SPIN</span></div>
    <div><span class="tube" style="--c:#c8262b" role="img" aria-label="Red top tube"></span><span class="hd rd">Red Top</span><p class="tt">Drug levels, Lithium, Digoxin, Serology, Allergy panel, Titers</p><span class="lb y">SPIN</span></div>
    <div><span class="tube" style="--c:#4a7be0" role="img" aria-label="Light blue top tube"></span><span class="hd bl">Light Blue</span><p class="tt">PT, INR, PTT, Fibrinogen, D-Dimer. Fill to line, invert 4x</p><span class="lb y">SPIN</span></div>
    <div><span class="tube" style="--c:#888" role="img" aria-label="Gray top tube"></span><span class="hd" style="background:#bbb">Gray Top</span><p class="tt">Glucose, Lactic acid. Keep on ice, deliver within 1 hour</p><span class="lb rd">ICE</span></div>
    <div><span class="tube" style="--c:#2e8b57" role="img" aria-label="Green top tube"></span><span class="hd" style="background:#9fd4b0">Green</span><p class="tt">Ammonia, Chromosome, Plasma chem. Wait 30 minutes after draw</p><span class="lb y">SPIN</span></div>
  </div>
</section>

<section class="page c4 r1">
  <div class="tab-bottom">Tabs Here - This portion will be trimmed off</div>
</section>

<!-- Page 25: PGX cover -->
<section class="page c1 r2">
  <div class="img" style="position:absolute;inset:0 10px 0 0;background:linear-gradient(160deg,#f2f4f6,#c4ccd4 55%,#7c8b99)" role="img" aria-label="Scientist in a lab coat examining a test tube beside a microscope"></div>
  <svg style="position:absolute;left:0;top:0" width="146" height="190" viewBox="0 0 146 190" aria-hidden="true">
    <polygon points="0,0 146,0 146,8 0,62" fill="#0054AA"/>
    <polygon points="0,62 146,8 146,11 0,65" fill="#7BADD7"/>
    <polygon points="0,65 146,11 146,60 0,100" fill="#ffffff"/>
  </svg>
  <div class="brand white" style="position:absolute;left:10px;top:20px;font-size:5px"><i style="width:5px;height:5px"></i>Harbor Point Labs</div>
  <div class="h" style="position:absolute;left:49px;top:58px;font-size:11px">PGX Testing</div>
  <div class="tab-side right"><span>Tabs Here - This portion will be trimmed off</span></div>
  <div class="folio r">25</div>
</section>

<section class="page c2 r2">
  <div class="tab-side left"><span>Tabs Here - This portion will be trimmed off</span></div>
  <div class="folio l">26</div>
</section>

<!-- Page 27: drug response -->
<section class="page c3 r2">
  <div style="position:absolute;left:2px;top:0;width:67px;bottom:7px;background:var(--blue);padding:4px 3px">
    <div style="background:#fff;padding:1.5px;text-align:center">
      <div class="h" style="font-size:3.2px">What are Drug Response Testing?</div>
    </div>
    <p class="tt" style="color:#fff;text-align:center;margin:1.5px 0">Pharmacogenomic (PGX) or Drug Response Testing is a simple non-invasive cheek swab that tests how your body will respond to medication based on your genetic makeup.</p>
    <div style="background:#fff;text-align:center" class="h"><span style="font-size:3.2px">Cost Savings</span></div>
    <p class="tt" style="color:#fff;margin:1.5px 0">☑ The potential savings over time outweigh the cost of drug response testing by more than two-fold.<br>☑ On average, residents saved on care after using PGX results to guide treatment.</p>
    <svg style="background:#fff;display:block" width="61" height="46" viewBox="0 0 61 46" role="img" aria-label="Bar chart of drug costs over three years">
      <text x="30" y="5" font-size="2" text-anchor="middle">■ Drug Reductions ■ Drug Replacements</text>
      <line x1="9" y1="40" x2="58" y2="40" stroke="#999" stroke-width=".3"/>
      <g font-size="1.6" fill="#666"><text x="1" y="12">$8,000</text><text x="1" y="22">$5,000</text><text x="1" y="32">$2,000</text><text x="30" y="44">Years</text></g>
      <rect x="14" y="22" width="5" height="18" fill="#e0262b"/><rect x="19" y="28" width="5" height="12" fill="#999"/>
      <rect x="30" y="14" width="5" height="26" fill="#e0262b"/><rect x="35" y="24" width="5" height="16" fill="#999"/>
      <rect x="46" y="9" width="5" height="31" fill="#e0262b"/><rect x="51" y="20" width="5" height="20" fill="#999"/>
    </svg>
    <svg style="background:#fff;display:block;margin-top:3px" width="61" height="44" viewBox="0 0 61 44" role="img" aria-label="Pie chart of savings by specialty">
      <circle cx="41" cy="19" r="13" fill="#e0262b"/>
      <path d="M41 19 L41 6 A13 13 0 0 0 28.5 15.5 Z" fill="#444"/>
      <path d="M41 19 L28.5 15.5 A13 13 0 0 0 33 29.5 Z" fill="#999"/>
      <g font-size="1.7"><rect x="3" y="10" width="2" height="2" fill="#e0262b"/><text x="6" y="11.7">Psychiatric</text><rect x="3" y="14" width="2" height="2" fill="#444"/><text x="6" y="15.7">Neurology</text><rect x="3" y="18" width="2" height="2" fill="#999"/><text x="6" y="19.7">Cardiovascular</text><rect x="3" y="22" width="2" height="2" fill="#ccc"/><text x="6" y="23.7">Urology</text></g>
      <text x="30" y="38" font-size="1.5" text-anchor="middle" fill="#555">Study of PGX use in a long-term care facility</text>
    </svg>
    <p class="tt" style="color:#fff;text-align:center;margin-top:3px">1200 LAKEVIEW AVE, SUITE 300, EASTBROOK</p>
  </div>
  <div style="position:absolute;left:73px;top:8px;width:70px">
    <div class="brand" style="justify-content:center;font-size:5.5px"><i style="width:6px;height:6px"></i>Harbor Point Labs</div>
    <div class="h" style="font-size:3.3px;text-align:center;margin-top:4px">What are the benefits of PGX Drug Response Testing?</div>
    <p class="tt" style="margin-top:1.5px">• Your DNA doesn't change, so a one-time test is all you'll ever need<br>• Reduce overall prescriptions<br>• No more trial and error means getting the right medication the first time<br>• Avoid costly hospitalizations by decreasing patient falls and adverse drug reactions</p>
    <div class="h" style="font-size:3.3px;text-align:center;margin-top:4px">Pharmacogenomics (PGX) = Drug Response Testing</div>
    <div style="display:flex;gap:2px;margin-top:2px">
      <p class="tt" style="flex:1"><b>Traditional Method of Prescribing Medicine</b><br>A standard dose that works for most people</p>
      <div style="width:10px;height:14px;background:var(--pale);border-radius:2px" role="img" aria-label="Medication capsule icon"></div>
      <p class="tt" style="flex:1">This is the correct dose for many patients. This medication may not work at all for some. This dose is too high for some patients.</p>
    </div>
    <p class="tt" style="margin-top:3px"><b>Prescribing Medicine While Incorporating PGX</b><br>Identifying the best medication at the optimal dose</p>
    <div style="display:flex;gap:2px;margin-top:2px">
      <div style="width:16px;height:18px;background:var(--mist);border-radius:2px" role="img" aria-label="Capsule and DNA icon"></div>
      <p class="tt" style="flex:1">Standard dose<br>Different medication<br>Lower dose<br>Higher dose</p>
    </div>
    <p class="tt" style="color:var(--blue);margin-top:3px;text-align:center">Drug response testing tells your doctor how YOU will respond to a certain medication, so they can use an alternative based on your DNA.</p>
    <p class="tt" style="color:var(--blue);margin-top:5px;text-align:center">85 MERIDIAN PLAZA, SUITE 410, EASTBROOK</p>
  </div>
  <div class="tab-side right"><span>Tabs Here - This portion will be trimmed off</span></div>
  <div class="folio r">27</div>
</section>

<!-- Page 28: postpartum -->
<section class="page c4 r2">
  <div class="tab-side left"><span>Tabs Here - This portion will be trimmed off</span></div>
  <div style="position:absolute;left:26px;right:9px;top:10px">
    <div class="h" style="font-size:5.2px">POSTPARTUM PGX BENEFITS</div>
    <div style="height:54px;margin-top:4px;background:linear-gradient(135deg,#e6e0da,#9a9591 55%,#5e636b)" role="img" aria-label="Mother holding her baby"></div>
    <p class="tt" style="margin-top:3px">Pharmacogenomic (PGx) testing for postpartum depression (PPD) can improve treatment outcomes by reducing the trial and error approach to medication selection. By analyzing how a person's genes affect their response to medication, PGx tests can help providers choose a more effective medication and dosage with fewer side effects.</p>
    <div class="h" style="font-size:3.7px;margin-top:4px">How PGx testing helps with postpartum depression</div>
    <p class="tt" style="margin-top:2px">For new mothers, PGx testing can address several key clinical and emotional concerns:<br>• Reduced trial-and-error: Many psychiatric medications, particularly antidepressants, have a low initial success rate. PGx testing can shorten the time it takes to find an effective treatment, which is critical for new mothers experiencing the severe and time-sensitive symptoms of PPD.<br>• Reduced adverse effects: The test can identify gene variants that cause a person to metabolize certain medications too slowly or too quickly, which can lead to adverse drug reactions or ineffective treatment.<br>• Informed decision-making for breastfeeding: Test results can help alleviate a mother's anxiety about drug metabolites passing into breast milk and potentially harming her infant.<br>• Personalized treatment plan: PGx testing can inform medication choices for mood disorders like PPD, helping a provider select a medication and dose that suits the patient.<br>• Durable effects: Studies suggest that PGx-guided treatment can lead to more lasting symptom improvement and higher remission rates compared to traditional prescribing methods.</p>
  </div>
  <div class="folio l">28</div>
</section>

<!-- Page 29: PGx testing guide -->
<section class="page c1 r3">
  <div style="position:absolute;left:7px;right:14px;top:7px">
    <div style="display:flex;justify-content:space-between;align-items:flex-start">
      <div><div class="h" style="font-size:4.6px">Pharmacogenomic (PGx) Testing</div>
      <div style="font-size:2.5px;font-weight:700">Tests Guide Appropriate Drug Selection and Dosing</div></div>
      <span style="width:24px;height:9px;background:var(--pale);border-radius:1px" role="img" aria-label="Partner badge"></span>
    </div>
    <p class="tt" style="margin-top:3px"><b>Pharmacogenomic (PGx) testing</b> (also known as pharmacogenomic biomarker testing) is a component of precision medicine that involves examining a patient's inherited genes to detect variations that may impact the way a drug is broken down, absorbed, and used within the body. Sometimes these variations can impact how patients with the same disease respond to treatment.</p>
    <div class="h" style="font-size:2.9px;margin-top:3px">Prescribing Without<br>Pharmacogenomic Testing</div>
    <div style="display:flex;gap:3px;margin-top:1.5px">
      <div style="flex:1.1;height:28px;background:var(--mist)" role="img" aria-label="Same drug and dose given to same disease patients with varied responses"></div>
      <p class="tt" style="flex:1;background:var(--pale);padding:1.5px"><b>Some gene-cancer drug interactions can have a significant impact on patient outcomes.</b> Certain variations in the DPYD gene have been linked to a higher risk of mortality from cancer drugs. Toxicity from some commonly used drugs is estimated to be responsible for more than 1,300 deaths per year.</p>
    </div>
    <p class="tt" style="margin-top:2px"><b>PGx testing can lead to better clinical outcomes for people with cancer</b> by improving the effectiveness of treatment or by reducing the risk of adverse drug reactions that can cause a patient to stop treatment.</p>
    <div class="h" style="font-size:2.9px;margin-top:3px">Prescribing With<br>Pharmacogenomic Testing</div>
    <div style="display:flex;gap:3px;margin-top:1.5px">
      <p class="tt" style="width:24px;background:var(--pale);padding:1.5px">By connecting patients to the right treatment and the right dose at the right time, PGx-guided cancer treatment can also be cost effective.</p>
      <div style="flex:1;height:32px;background:var(--mist)" role="img" aria-label="Diagram of patients receiving adjusted doses after PGx testing"></div>
    </div>
    <p class="tt" style="margin-top:2px;color:#666">1. Review of clinical evidence and implementation. 2. Cost-effectiveness analysis of genotyping before therapy. 3. Economic model of testing before prescribing.</p>
    <p class="tt" style="margin-top:1.5px">To learn more about cancer biomarkers and how they are used, visit our resource line or call 555 014 2290.</p>
  </div>
  <div class="tab-side right"><span>Tabs Here - This portion will be trimmed off</span></div>
  <div class="folio r">29</div>
</section>

<!-- Page 30: requisition -->
<section class="page c2 r3">
  <div class="tab-side left"><span>Tabs Here - This portion will be trimmed off</span></div>
  <div style="position:absolute;left:18px;right:6px;top:8px">
    <div style="display:flex;justify-content:space-between;align-items:flex-start">
      <p class="tt">1200 Lakeview Ave, Suite 300<br>Eastbrook<br>Phone: 555 014 2290<br>Fax: 555 014 2291<br>support@harborpointlabs.example</p>
      <div class="brand" style="font-size:4px;margin-right:20px"><i style="width:4px;height:4px"></i>Harbor Point Labs</div>
    </div>
    <div style="display:grid;grid-template-columns:1fr 1fr;gap:1px;margin-top:2px">
      <div><div class="band">PATIENT INFORMATION</div>
        <div class="form-row">FIRST NAME:</div><div class="form-row">LAST NAME:</div><div class="form-row">DOB: XXX &nbsp; SEX: ☐ M ☐ F</div><div class="form-row">ADDRESS:</div><div class="form-row">CITY: &nbsp; STATE: &nbsp; ZIP:</div><div class="form-row">PHONE: &nbsp; EMAIL:</div>
      </div>
      <div><div class="band">PROVIDER INFORMATION</div>
        <div class="form-row">PHYSICIAN:</div><div class="form-row">NPI:</div><div class="form-row">PRACTICE:</div><div class="form-row">PHONE:</div><div class="form-row">FAX:</div><div class="form-row">ACCOUNT #:</div>
      </div>
    </div>
    <div style="display:grid;grid-template-columns:1fr 1fr;gap:1px">
      <div><div class="band">ANCESTRY</div><p class="tt">☐ African American ☐ Hispanic ☐ East Asian ☐ Caucasian ☐ Pacific Islander ☐ South Asian ☐ Native American ☐ Other</p></div>
      <div><div class="band">SPECIMEN INFORMATION</div><p class="tt" style="background:#fff7a8">DATE OF COLLECTION: &nbsp; TIME: ☐ AM ☐ PM<br>SPECIMEN TYPE: ☐ Buccal Swab &nbsp; COLLECTOR:</p></div>
    </div>
    <div class="band">INSURANCE INFORMATION</div>
    <div class="form-row">☐ Insurance &nbsp; ☐ Client Bill &nbsp; ☐ Self-Pay</div>
    <div class="form-row">CARRIER: &nbsp; GROUP #: &nbsp; POLICY #:</div>
    <div class="form-row">NAME OF INSURED: &nbsp; DOB OF INSURED: &nbsp; RELATIONSHIP:</div>
    <div class="band">TEST SELECTION</div>
    <p class="tt" style="display:grid;grid-template-columns:1fr 1fr;gap:2px">Current Rx or considering Rx: Please list the medications you would like reviewed. Include ICD-10 codes for each.<span>Provider Notes: Please describe in as much detail as possible why you are evaluating the medication for selection or avoidance.</span></p>
    <div class="form-row" style="grid-template-columns:repeat(7,1fr);font-weight:400">PGX PANEL:<span>CYP2C9</span><span>CYP2D6</span><span>COMT</span><span>CYP3A4</span><span>VKORC1</span><span>MTHFR</span></div>
    <div class="form-row" style="grid-template-columns:repeat(7,1fr);font-weight:400">SUB PANEL:<span>CYP2C19</span><span>APOE</span><span>CYP1A2</span><span>F2</span><span>F5</span><span>SLCO1B1</span></div>
    <div class="band">PHYSICIAN AUTHORIZATION</div>
    <p class="tt">I have reviewed the patient's history and medications and determined that this test is medically necessary. The results will be used in the management of the patient's treatment. I confirm the patient has given informed consent for genetic testing.</p>
    <div class="form-row">PHYSICIAN SIGNATURE: &nbsp;&nbsp;&nbsp;&nbsp;&nbsp;&nbsp; DATE:</div>
    <div class="band">PATIENT AUTHORIZATION</div>
    <p class="tt">I authorize the laboratory to perform the test ordered and to release results to my provider. I assign benefits to the laboratory and understand I may be responsible for charges not covered by my plan. I understand my sample may be kept for quality purposes.</p>
    <div class="form-row">PATIENT SIGNATURE: &nbsp;&nbsp;&nbsp;&nbsp;&nbsp;&nbsp; DATE:</div>
  </div>
  <div class="folio l">30</div>
</section>

<!-- Page 31: medication codes CYP2D6 -->
<section class="page c3 r3">
  <div style="position:absolute;left:7px;right:13px;top:10px">
    <div class="band">MEDICATIONS &amp; ICD-10 CODES REQUIRED FOR PHARMACOGENOMIC TESTING</div>
    <p class="tt" style="background:var(--mist);padding:1px">Provider Notes: Please check each current or considered medication and at least one diagnosis code. Codes must be supported in the patient record.</p>
    <div class="band sky">CYP2D6</div>
    <div class="drugs" style="column-count:4;height:150px">
      <p class="sec">TRICYCLIC ANTIDEPRESSANTS</p>
      <p><b>☐ Amitriptyline</b>☐ Current ☐ Considering<br>☐ F32.9 ☐ F33.1 ☐ F41.1<br>☐ G43.9 ☐ M79.7 ☐ Other</p>
      <p><b>☐ Clomipramine</b>☐ Current ☐ Considering<br>☐ F42.2 ☐ F32.9 ☐ F41.0<br>☐ F33.2 ☐ Other</p>
      <p><b>☐ Desipramine</b>☐ Current ☐ Considering<br>☐ F32.9 ☐ F90.0 ☐ Other</p>
      <p><b>☐ Doxepin</b>☐ Current ☐ Considering<br>☐ F32.9 ☐ F41.1 ☐ G47.00<br>☐ L29.9 ☐ Other</p>
      <p><b>☐ Imipramine</b>☐ Current ☐ Considering<br>☐ F32.9 ☐ N39.44 ☐ Other</p>
      <p><b>☐ Nortriptyline</b>☐ Current ☐ Considering<br>☐ F32.9 ☐ G43.9 ☐ M79.2<br>☐ F17.2 ☐ Other</p>
      <p class="sec">ANTIPSYCHOTICS</p>
      <p><b>☐ Aripiprazole</b>☐ Current ☐ Considering<br>☐ F20.9 ☐ F31.9 ☐ F84.0<br>☐ F95.2 ☐ Other</p>
      <p><b>☐ Brexpiprazole</b>☐ Current ☐ Considering<br>☐ F20.9 ☐ F33.1 ☐ Other</p>
      <p><b>☐ Haloperidol</b>☐ Current ☐ Considering<br>☐ F20.9 ☐ F95.2 ☐ R41.0</p>
      <p><b>☐ Iloperidone</b>☐ Current ☐ Considering<br>☐ F20.9 ☐ F31.1 ☐ Other</p>
      <p><b>☐ Perphenazine</b>☐ Current ☐ Considering<br>☐ F20.9 ☐ R11.2 ☐ Other</p>
      <p><b>☐ Pimozide</b>☐ Current ☐ Considering<br>☐ F95.2 ☐ Other</p>
      <p><b>☐ Risperidone</b>☐ Current ☐ Considering<br>☐ F20.9 ☐ F31.9 ☐ F84.0</p>
      <p class="sec">ADHD</p>
      <p><b>☐ Atomoxetine</b>☐ Current ☐ Considering<br>☐ F90.0 ☐ F90.1 ☐ F90.2</p>
      <p><b>☐ Amphetamine</b>☐ Current ☐ Considering<br>☐ F90.9 ☐ G47.411</p>
      <p class="sec">OPIOIDS</p>
      <p><b>☐ Codeine</b>☐ Current ☐ Considering<br>☐ G89.29 ☐ M54.5 ☐ R05</p>
      <p><b>☐ Tramadol</b>☐ Current ☐ Considering<br>☐ G89.29 ☐ M25.50 ☐ M54.5</p>
      <p><b>☐ Oxycodone</b>☐ Current ☐ Considering<br>☐ G89.4 ☐ M79.7 ☐ Other</p>
      <p><b>☐ Hydrocodone</b>☐ Current ☐ Considering<br>☐ G89.29 ☐ M54.2</p>
      <p class="sec">ANTIEMETICS</p>
      <p><b>☐ Ondansetron</b>☐ Current ☐ Considering<br>☐ R11.0 ☐ R11.2 ☐ Z51.11</p>
      <p><b>☐ Metoclopramide</b>☐ Current ☐ Considering<br>☐ K31.84 ☐ K21.9</p>
      <p class="sec">CARDIOVASCULAR</p>
      <p><b>☐ Carvedilol</b>☐ Current ☐ Considering<br>☐ I10 ☐ I50.9 ☐ I25.10</p>
      <p><b>☐ Metoprolol</b>☐ Current ☐ Considering<br>☐ I10 ☐ I48.91 ☐ I20.9</p>
      <p><b>☐ Propafenone</b>☐ Current ☐ Considering<br>☐ I48.0 ☐ I47.1</p>
      <p><b>☐ Flecainide</b>☐ Current ☐ Considering<br>☐ I48.91 ☐ I47.2</p>
      <p class="sec">ONCOLOGY</p>
      <p><b>☐ Tamoxifen</b>☐ Current ☐ Considering<br>☐ C50.919 ☐ Z17.0 ☐ Z80.3</p>
      <p><b>☐ Fluoxetine</b>☐ Current ☐ Considering<br>☐ F32.9 ☐ F42.2 ☐ F50.2</p>
      <p><b>☐ Paroxetine</b>☐ Current ☐ Considering<br>☐ F41.1 ☐ F43.10 ☐ N95.1</p>
      <p><b>☐ Venlafaxine</b>☐ Current ☐ Considering<br>☐ F32.9 ☐ F41.1 ☐ F40.10</p>
      <p><b>☐ Vortioxetine</b>☐ Current ☐ Considering<br>☐ F32.9 ☐ F33.1 ☐ Other</p>
    </div>
  </div>
  <div class="tab-side right"><span>Tabs Here - This portion will be trimmed off</span></div>
  <div class="folio r">31</div>
</section>

<!-- Page 32: CYP2C19 / CYP2C9 -->
<section class="page c4 r3">
  <div class="tab-side left"><span>Tabs Here - This portion will be trimmed off</span></div>
  <div style="position:absolute;left:17px;right:6px;top:10px">
    <div class="band sky">CYP2C19</div>
    <div class="drugs" style="column-count:4;height:104px">
      <p class="sec">ANTICONVULSANTS</p>
      <p><b>☐ Brivaracetam</b>☐ Current ☐ Considering<br>☐ G40.909 ☐ G40.219 ☐ Other</p>
      <p><b>☐ Clobazam</b>☐ Current ☐ Considering<br>☐ G40.812 ☐ G40.909</p>
      <p><b>☐ Diazepam</b>☐ Current ☐ Considering<br>☐ F41.1 ☐ G40.901 ☐ M62.838</p>
      <p class="sec">ANTIPLATELETS</p>
      <p><b>☐ Clopidogrel</b>☐ Current ☐ Considering<br>☐ I25.10 ☐ I21.4 ☐ I63.9<br>☐ Z95.5 ☐ Other</p>
      <p class="sec">SSRIS</p>
      <p><b>☐ Citalopram</b>☐ Current ☐ Considering<br>☐ F32.9 ☐ F41.1 ☐ F41.0</p>
      <p><b>☐ Escitalopram</b>☐ Current ☐ Considering<br>☐ F32.9 ☐ F41.1 ☐ F42.2</p>
      <p><b>☐ Sertraline</b>☐ Current ☐ Considering<br>☐ F32.9 ☐ F43.10 ☐ F42.2</p>
      <p class="sec">TRICYCLICS</p>
      <p><b>☐ Amitriptyline</b>☐ Current ☐ Considering<br>☐ F32.9 ☐ G43.9 ☐ M79.7</p>
      <p><b>☐ Clomipramine</b>☐ Current ☐ Considering<br>☐ F42.2 ☐ F32.9</p>
      <p><b>☐ Doxepin</b>☐ Current ☐ Considering<br>☐ G47.00 ☐ L29.9</p>
      <p><b>☐ Imipramine</b>☐ Current ☐ Considering<br>☐ F32.9 ☐ N39.44</p>
      <p class="sec">PROTON PUMP INHIBITORS</p>
      <p><b>☐ Omeprazole</b>☐ Current ☐ Considering<br>☐ K21.9 ☐ K25.9 ☐ K29.70</p>
      <p><b>☐ Pantoprazole</b>☐ Current ☐ Considering<br>☐ K21.0 ☐ K21.9 ☐ K22.70</p>
      <p><b>☐ Lansoprazole</b>☐ Current ☐ Considering<br>☐ K21.9 ☐ K27.9</p>
      <p><b>☐ Dexlansoprazole</b>☐ Current ☐ Considering<br>☐ K21.0 ☐ K21.9</p>
      <p class="sec">ANTIFUNGALS</p>
      <p><b>☐ Voriconazole</b>☐ Current ☐ Considering<br>☐ B44.9 ☐ B37.9 ☐ Other</p>
    </div>
    <div class="band sky" style="margin-top:1px">CYP2C9</div>
    <div class="drugs" style="column-count:4;height:60px">
      <p class="sec">NSAIDS</p>
      <p><b>☐ Celecoxib</b>☐ Current ☐ Considering<br>☐ M19.90 ☐ M06.9 ☐ M54.5</p>
      <p><b>☐ Flurbiprofen</b>☐ Current ☐ Considering<br>☐ M19.90 ☐ M06.9</p>
      <p><b>☐ Meloxicam</b>☐ Current ☐ Considering<br>☐ M19.90 ☐ M06.9 ☐ M45.9</p>
      <p><b>☐ Piroxicam</b>☐ Current ☐ Considering<br>☐ M19.90 ☐ M06.9</p>
      <p class="sec">ANTICONVULSANTS</p>
      <p><b>☐ Phenytoin</b>☐ Current ☐ Considering<br>☐ G40.909 ☐ G40.401</p>
      <p class="sec">ANTICOAGULANTS</p>
      <p><b>☐ Warfarin</b>☐ Current ☐ Considering<br>☐ I48.91 ☐ I26.99 ☐ I82.409<br>☐ Z79.01 ☐ Other</p>
      <p class="sec">IMMUNOMODULATORS</p>
      <p><b>☐ Siponimod</b>☐ Current ☐ Considering<br>☐ G35 ☐ Other</p>
      <p class="sec">CARDIOVASCULAR</p>
      <p><b>☐ Fluvastatin</b>☐ Current ☐ Considering<br>☐ E78.5 ☐ E78.00</p>
    </div>
  </div>
  <div class="folio l">32</div>
</section>

<!-- Page 33: SLCO1B1 and notes -->
<section class="page c1 r4">
  <div style="position:absolute;left:7px;right:13px;top:12px">
    <div class="band sky">SLCO1B1</div>
    <div class="drugs" style="column-count:3;height:38px">
      <p class="sec">STATINS</p>
      <p><b>☐ Atorvastatin</b>☐ Current ☐ Considering<br>☐ E78.5 ☐ E78.00 ☐ I25.10</p>
      <p><b>☐ Rosuvastatin</b>☐ Current ☐ Considering<br>☐ E78.5 ☐ E78.01</p>
      <p><b>☐ Levastatin</b>☐ Current ☐ Considering<br>☐ E78.5 ☐ E78.2</p>
      <p><b>☐ Pitavastatin</b>☐ Current ☐ Considering<br>☐ E78.5 ☐ E78.00</p>
      <p><b>☐ Pravastatin</b>☐ Current ☐ Considering<br>☐ E78.5 ☐ I63.9</p>
      <p><b>☐ Simvastatin</b>☐ Current ☐ Considering<br>☐ E78.5 ☐ E78.00</p>
    </div>
    <div class="band">OTHER MEDICATIONS, NOTES, AND DIAGNOSTIC CODES (ICD-10)</div>
    <div style="height:36px;border:.4px solid var(--sky);background:repeating-linear-gradient(#fff 0 3.6px,#b9c3cc 3.6px 4px)"></div>
    <div class="tt" style="display:flex;justify-content:space-around;padding:1px 0">☐ Medications Attached<span>☐ ICD-10 Codes &amp; Notes Attached</span></div>
    <div class="band" style="margin-top:2px">FACTOR II &amp; FACTOR V DIAGNOSTIC CODES (INDEPENDENT OF MEDICATION)</div>
    <p class="tt" style="background:var(--mist);padding:1px">ICD-10 Diagnosis: At least one diagnosis code is required. Select all that apply for thrombophilia risk evaluation.</p>
    <div class="codes">
      <span>☐ D68.51</span><span>☐ D68.52</span><span>☐ D68.59</span><span>☐ D68.61</span><span>☐ D68.62</span><span>☐ D68.69</span><span>☐ I26.99</span><span>☐ I63.9</span>
      <span>☐ I80.10</span><span>☐ I80.209</span><span>☐ I82.409</span><span>☐ I82.90</span><span>☐ N96</span><span>☐ O03.9</span><span>☐ O26.20</span><span>☐ O36.5</span>
      <span>☐ O45.90</span><span>☐ Z79.01</span><span>☐ Z82.49</span><span>☐ Z83.2</span><span>☐ Z86.718</span><span>☐ Z86.711</span><span>☐ Z86.73</span><span>☐ I21.4</span>
      <span>☐ I74.3</span><span>☐ I81</span><span>☐ I82.210</span><span>☐ I82.220</span><span>☐ O22.30</span><span>☐ O87.1</span><span>☐ Z31.441</span><span>☐ Other</span>
    </div>
  </div>
  <div class="tab-side right"><span>Tabs Here - This portion will be trimmed off</span></div>
  <div class="folio r">33</div>
</section>

<!-- Page 34: test menu -->
<section class="page c2 r4">
  <div class="tab-side left"><span>Tabs Here - This portion will be trimmed off</span></div>
  <div style="position:absolute;left:17px;right:5px;top:10px">
    <div class="brand" style="justify-content:center;font-size:4.5px"><i style="width:4.5px;height:4.5px"></i>Harbor Point Labs</div>
    <div style="font-family:'Montserrat',sans-serif;font-weight:600;font-size:5.5px;text-align:center;margin-top:3px">PGX TEST MENU</div>
    <div class="tt" style="display:grid;grid-template-columns:repeat(6,1fr);gap:2px;margin-top:5px;font-size:1.8px;line-height:1.55">
      <div><span class="pill">Analgesia</span><br>Acetaminophen<br>Carisoprodol<br>Celecoxib<br>Codeine<br>Diclofenac<br>Flurbiprofen<br>Hydrocodone<br>Ibuprofen<br>Meloxicam<br>Methadone<br>Morphine<br>Naproxen<br>Oxycodone<br>Piroxicam<br>Tramadol<br>Tapentadol<br><span class="pill">Autoimmune</span><br>Azathioprine<br>Siponimod<br>Tacrolimus<br>Leflunomide</div>
      <div><span class="pill">Cancer</span><br>Capecitabine<br>Fluorouracil<br>Irinotecan<br>Tamoxifen<br>Nilotinib<br><span class="pill">Cardiovascular</span><br>Amlodipine<br>Atorvastatin<br>Carvedilol<br>Clopidogrel<br>Flecainide<br>Metoprolol<br>Prasugrel<br>Propafenone<br>Rosuvastatin<br>Simvastatin<br>Warfarin<br><span class="pill">Endocrinology</span><br>Glipizide<br>Glyburide<br>Tolbutamide</div>
      <div><span class="pill">Gastro</span><br>Dexlansoprazole<br>Esomeprazole<br>Lansoprazole<br>Metoclopramide<br>Omeprazole<br>Ondansetron<br>Pantoprazole<br>Rabeprazole<br><span class="pill">Infection</span><br>Efavirenz<br>Voriconazole<br>Atazanavir<br>Dapsone<br><span class="pill">Mental Health</span><br>Amitriptyline<br>Aripiprazole<br>Citalopram<br>Escitalopram<br>Fluoxetine<br>Sertraline</div>
      <div><br>Bupropion<br>Clomipramine<br>Desipramine<br>Doxepin<br>Duloxetine<br>Haloperidol<br>Imipramine<br>Lithium<br>Mirtazapine<br>Nortriptyline<br>Paroxetine<br>Quetiapine<br>Risperidone<br>Trazodone<br>Venlafaxine<br>Vortioxetine<br>Zolpidem<br>Atomoxetine<br>Amphetamine<br>Methylphenidate<br>Buspirone</div>
      <div><span class="pill">Neurology</span><br>Brivaracetam<br>Carbamazepine<br>Clobazam<br>Diazepam<br>Donepezil<br>Galantamine<br>Lacosamide<br>Lamotrigine<br>Phenytoin<br>Tetrabenazine<br>Valproic Acid<br><span class="pill">Other</span><br>Allopurinol<br>Atomoxetine<br>Eliglustat<br>Mavacamten<br>Pimozide<br>Tolterodine</div>
      <div><span class="pill">Rheumatology</span><br>Celecoxib<br>Flurbiprofen<br>Ibuprofen<br>Meloxicam<br>Methotrexate<br>Piroxicam<br><span class="pill">Urology</span><br>Darifenacin<br>Fesoterodine<br>Mirabegron<br>Solifenacin<br>Tamsulosin<br>Tolterodine</div>
    </div>
  </div>
  <div class="folio l">34</div>
</section>

<section class="page c3 r4">
  <div class="tab-side right"><span>Tabs Here - This portion will be trimmed off</span></div>
  <div class="folio r">35</div>
</section>

<!-- Page 36: medication summary -->
<section class="page c4 r4">
  <div class="tab-side left"><span>Tabs Here - This portion will be trimmed off</span></div>
  <div style="position:absolute;left:17px;right:6px;top:8px">
    <div style="display:flex;justify-content:space-between;align-items:flex-start">
      <div class="brand" style="font-size:4px"><i style="width:4px;height:4px"></i>Harbor Point Labs</div>
      <p class="tt" style="font-size:1.7px"><b>PATIENT INFORMATION</b><br>NAME: XXX<br>DOB: XXX<br>SEX AT BIRTH: XXX</p>
      <p class="tt" style="font-size:1.7px"><b>SPECIMEN DETAILS</b><br>ACCESSION: XXX<br>TYPE: Buccal<br>COLLECTED: XXX</p>
      <p class="tt" style="font-size:1.7px"><b>ORDERED BY</b><br>Provider XXX<br>GENERATED: XXX</p>
    </div>
    <div class="h" style="font-size:4px;margin-top:2px">MEDICATION SUMMARY TABLE</div>
    <p class="tt" style="font-size:1.7px">The Medication Summary Table lists medications with pharmacogenomic associations, organized by therapeutic area and drug-gene interaction. Review each medication in context of the patient's full clinical picture before making changes.</p>
    <div class="summary" style="grid-template-columns:5px repeat(6,1fr);margin-top:2px">
      <div></div><div class="alt"><b>① Standard precautions</b></div><div><b>Consider alternative</b></div><div><b>② Moderate drug-gene</b> May increase toxicity</div><div>May reduce efficacy</div><div>May increase dose</div><div class="alt"><b>③ Serious drug-gene</b></div>
      <div class="cat" style="height:30px">Analgesia</div><div class="alt">Acetaminophen Carisoprodol Diclofenac Ibuprofen Ketorolac Methadone Morphine Naproxen Oxymorphone Tapentadol</div><div></div><div></div><div></div><div></div><div class="alt">Amitriptyline Codeine Oxycodone Tramadol</div>
      <div class="cat" style="height:13px">Autoimmune</div><div class="alt">Methotrexate Leflunomide</div><div></div><div class="red">Azathioprine</div><div></div><div class="red">Tacrolimus</div><div class="alt"></div>
      <div class="cat" style="height:15px">Cancer</div><div class="alt">Anastrozole Letrozole Imatinib Exemestane</div><div></div><div></div><div></div><div></div><div class="alt"></div>
      <div class="cat" style="height:24px">Cardiovascular</div><div class="alt">Amlodipine Apixaban Atenolol Carvedilol Diltiazem Lisinopril Losartan Rivaroxaban</div><div class="red">Clopidogrel Propafenone</div><div class="red">Flecainide Warfarin</div><div class="red">Metoprolol</div><div class="red">Simvastatin Atorvastatin</div><div class="alt">Clopidogrel</div>
      <div class="cat" style="height:12px">Endocrine</div><div class="alt">Glipizide Metformin</div><div></div><div></div><div></div><div></div><div class="alt"></div>
      <div class="cat" style="height:16px">Gastro</div><div class="alt">Famotidine Ondansetron Metoclopramide Rabeprazole</div><div></div><div class="red">Dexlansoprazole Lansoprazole</div><div class="red">Omeprazole</div><div class="red">Esomeprazole Pantoprazole</div><div class="alt">Ondansetron</div>
    </div>
  </div>
  <div class="folio l">36</div>
</section>

<!-- Page 37: summary continued -->
<section class="page c1 r5">
  <div class="summary" style="position:absolute;left:10px;right:15px;top:10px;grid-template-columns:5px repeat(6,1fr)">
    <div class="cat" style="height:12px">Infection</div><div class="alt">Azithromycin Ciprofloxacin</div><div></div><div class="red">Efavirenz</div><div></div><div class="red">Voriconazole</div><div class="alt"></div>
    <div class="cat" style="height:46px">Mental Health</div><div class="alt">Aripiprazole Brexpiprazole Bupropion Buspirone Clonazepam Duloxetine Lorazepam Lurasidone Mirtazapine Olanzapine Quetiapine Trazodone Ziprasidone</div><div class="red">Doxepin Nortriptyline</div><div class="red">Citalopram Escitalopram Sertraline</div><div class="red">Paroxetine Fluoxetine</div><div class="red">Imipramine Clomipramine</div><div class="alt">Amitriptyline Clomipramine Desipramine Doxepin Imipramine Trimipramine</div>
    <div class="cat" style="height:40px">Neurology</div><div class="alt">Brivaracetam Carbamazepine Clobazam Diazepam Donepezil Galantamine Gabapentin Lacosamide Lamotrigine Levetiracetam Oxcarbazepine Pregabalin Topiramate Valproic Acid</div><div></div><div></div><div class="red">Clobazam</div><div></div><div class="alt">Phenytoin</div>
    <div class="cat" style="height:16px">Other</div><div class="alt">Allopurinol Colchicine Montelukast Sildenafil</div><div></div><div></div><div></div><div></div><div class="alt">Eliglustat</div>
    <div class="cat" style="height:18px">Rheumatology</div><div class="alt">Celecoxib Flurbiprofen Hydroxychloroquine Meloxicam Piroxicam Sulfasalazine</div><div></div><div></div><div></div><div></div><div class="alt"></div>
    <div class="cat" style="height:16px">Urology</div><div class="alt">Darifenacin Fesoterodine Mirabegron Solifenacin Tamsulosin Tolterodine</div><div></div><div></div><div></div><div></div><div class="alt"></div>
  </div>
  <div class="tab-side right"><span>Tabs Here - This portion will be trimmed off</span></div>
  <div class="folio r">37</div>
</section>

<section class="page c2 r5">
  <div class="tab-side left"><span>Tabs Here - This portion will be trimmed off</span></div>
  <div class="folio l">38</div>
</section>

<!-- Page 39: culture cover -->
<section class="page c3 r5">
  <div class="img" style="position:absolute;inset:0 10px 0 0;background:linear-gradient(150deg,#f4f5f6,#ddd5ce 50%,#7d8fa6)" role="img" aria-label="Smiling patient speaking with a clinician"></div>
  <svg style="position:absolute;left:0;top:0" width="146" height="190" viewBox="0 0 146 190" aria-hidden="true">
    <polygon points="0,0 146,0 146,4 0,52" fill="#0054AA"/>
    <polygon points="0,52 146,4 146,7 0,55" fill="#7BADD7"/>
    <polygon points="0,55 146,7 146,40 0,86" fill="#ffffff"/>
    <polygon points="0,182 146,160 146,190 0,190" fill="#0677BA"/>
  </svg>
  <div class="brand white" style="position:absolute;left:10px;top:16px;font-size:5px"><i style="width:5px;height:5px"></i>Harbor Point Labs</div>
  <div class="h" style="position:absolute;left:55px;top:58px;font-size:10.5px">Culture Testing</div>
  <div class="tab-side right"><span>Tabs Here - This portion will be trimmed off</span></div>
  <div class="folio r" style="color:#fff">39</div>
</section>

<section class="page c4 r5">
  <div class="tab-side left"><span>Tabs Here - This portion will be trimmed off</span></div>
  <div class="folio l">40</div>
</section>

</main>
</body>
</html>
```